Brochure required

Looking at getting business brochure designed for my solar sales company. i will require a range of products to be listed on the brochure I require a simple/ elegent / professional looking brochure.

I am happy to provide designer with all the required information that must go into the brochure. otherwise please visit www.quillebartow.com.au and view the products which i would like to allocate into the brochure aswell as our company logo and a little about me section

```html
<!DOCTYPE html>
<html lang="en">
<head>
<meta charset="utf-8">
<title>Solar Brochure Spread</title>
<link rel="stylesheet" href="https://fonts.googleapis.com/css2?family=Open+Sans:wght@400;600;700&display=swap">
<style>
  :root {
    --canvas: #e6e6e9;
    --paper: #ffffff;
    --brand-green: #16a37a;
    --accent-teal: #1fc39a;
    --title-blue: #1a86c8;
    --ink: #2b2b2b;
    --body-ink: #4a4a4a;
    --fold: #d4d4d8;
    --photo-array: #7f9ab8;
    --photo-tracker: #3a72c6;
  }
  * { box-sizing: border-box; margin: 0; padding: 0; }
  html, body {
    width: 1200px; height: 840px; overflow: hidden;
    background: var(--canvas);
    font-family: "Open Sans", Arial, sans-serif;
  }
  .spread {
    position: absolute; left: 170px; top: 116px;
    width: 860px; height: 608px;
    display: flex;
    box-shadow: 0 10px 30px rgba(0,0,0,0.12);
  }
  .page {
    position: relative; width: 430px; height: 608px;
    background: var(--paper); overflow: hidden;
  }
  .page--left { border-right: 1px solid var(--fold); }

  /* Left page */
  .cover-head { padding: 34px 34px 0; height: 96px; }
  .cover-title {
    color: var(--title-blue); font-weight: 700; font-size: 19px;
    letter-spacing: 0.5px; text-transform: uppercase; line-height: 1.15;
  }
  .cover-subtitle {
    color: var(--ink); font-weight: 400; font-size: 14px;
    letter-spacing: 0.5px; text-transform: uppercase; margin-top: 2px;
  }
  .intro-band {
    background: var(--brand-green); height: 142px;
    padding: 18px 34px 0; color: #fff;
  }
  .intro-heading { font-size: 18px; font-weight: 600; margin-bottom: 8px; }
  .intro-text { font-size: 8.5px; line-height: 1.5; text-align: justify; opacity: 0.95; }
  .photo { display: block; width: 100%; }
  .photo--array { height: 346px; background: var(--photo-array); }

  /* Right page */
  .feature { padding: 34px 30px 0 30px; height: 318px; }
  .feature-heading {
    color: var(--accent-teal); font-size: 16px; font-weight: 700;
    margin-bottom: 8px;
  }
  .feature-text {
    color: var(--body-ink); font-size: 9px; line-height: 1.5;
    text-align: justify; margin-bottom: 7px;
  }
  .photo--tracker { height: 240px; background: var(--photo-tracker); }
  .site-url {
    text-align: center; font-size: 15px; font-weight: 600;
    color: var(--ink); letter-spacing: 0.5px; margin-top: 14px;
  }
  .site-url .site-name { color: var(--accent-teal); }
</style>
</head>
<body>
  <main class="spread">
    <section class="page page--left">
      <header class="cover-head">
        <h1 class="cover-title">Quis Nostrum Exercitationem</h1>
        <p class="cover-subtitle">Ullam Corporis Suscipit</p>
      </header>
      <div class="intro-band">
        <h2 class="intro-heading">At Vero Eos Et Accusamus Et</h2>
        <p class="intro-text">Nam libero tempore cum soluta nobis est eligendi optio cumque nihil impedit quo minus id quod maxime placeat facere possimus omnis voluptas assumenda est omnis dolor repellendus temporibus autem quibusdam et aut officiis debitis aut rerum necessitatibus saepe eveniet ut et voluptates repudiandae sint et molestiae non recusandae itaque earum rerum hic tenetur a sapiente delectus.</p>
      </div>
      <div class="photo photo--array" role="img" aria-label="Photograph of rows of solar panels on a green field under a cloudy sky"></div>
    </section>

    <section class="page page--right">
      <article class="feature">
        <h2 class="feature-heading">Dignissimos Ducimus Qui</h2>
        <p class="feature-text">Blanditiis praesentium voluptatum deleniti atque corrupti quos dolores et quas molestias excepturi sint occaecati cupiditate non provident, similique sunt in culpa qui officia deserunt mollitia animi, id est laborum et dolorum fuga. Et harum quidem rerum facilis est et expedita distinctio. Nam libero tempore, cum soluta nobis est eligendi optio cumque nihil impedit quo minus id quod maxime placeat facere possimus.</p>
        <p class="feature-text">Omnis voluptas assumenda est, omnis dolor repellendus. Temporibus autem quibusdam et aut officiis debitis aut rerum necessitatibus saepe eveniet ut et voluptates repudiandae sint et molestiae non recusandae. Itaque earum rerum hic tenetur a sapiente delectus, ut aut reiciendis voluptatibus maiores alias consequatur aut perferendis doloribus asperiores repellat.</p>
        <p class="feature-text">Sed ut perspiciatis unde omnis iste natus error sit voluptatem accusantium doloremque laudantium, totam rem aperiam, eaque ipsa quae ab illo inventore veritatis et quasi architecto beatae vitae dicta sunt explicabo. Nemo enim ipsam voluptatem quia voluptas sit aspernatur aut odit aut fugit, sed quia consequuntur magni dolores eos qui ratione.</p>
      </article>
      <div class="photo photo--tracker" role="img" aria-label="Photograph of a single solar tracker panel on grass against a blue sky"></div>
      <p class="site-url">www.<span class="site-name">quillebartow</span>.com.au</p>
    </section>
  </main>
</body>
</html>
```